Local Roofing/Construction company business needs new biz card design

We need a new business card design, current cards are from the start of this operation and generic at best. We are a local Construction Company (General Contractor) with a majority of our work originating from insurance claims-exterior finish work is the main focus (Roofs-Siding-Gutters etc). Heavily involved with homeowners and the low ball offers they receive from insurance company's after a insurable event takes place. I have attached some of our original logo file(s) below.

```html
<!DOCTYPE html>
<html lang="en">
<head>
<meta charset="utf-8">
<title>Holloway Build Co. — Business Card</title>
<link rel="stylesheet" href="https://fonts.googleapis.com/css2?family=Montserrat:wght@400;600;700&display=swap">
<style>
  :root {
    --backdrop: #161717;
    --card: #0e1c1f;
    --green: #4fb16b;
    --ink: #eef1ef;
  }
  * { box-sizing: border-box; margin: 0; padding: 0; }
  html, body {
    width: 1200px; height: 1059px; overflow: hidden;
    background: var(--backdrop);
    font-family: "Montserrat", Arial, sans-serif;
    color: var(--ink);
  }
  .card {
    position: absolute;
    width: 690px; height: 392px;
    background: var(--card);
    border-radius: 18px;
    box-shadow: 0 10px 24px rgba(0,0,0,0.55);
    overflow: hidden;
  }
  .card-front { left: 256px; top: 89px; }
  .card-back { left: 255px; top: 548px; }

  .brand {
    position: absolute; right: 40px; top: 62px;
    display: flex; align-items: center; gap: 10px;
    color: var(--green); font-weight: 700; font-size: 22px;
    letter-spacing: 0.5px; text-transform: uppercase;
  }
  .brand-square { width: 18px; height: 18px; background: var(--green); }

  .name-accent {
    position: absolute; left: 0; top: 206px;
    width: 21px; height: 41px; background: var(--green);
  }
  .person { position: absolute; left: 37px; top: 202px; }
  .person-name {
    color: var(--green); font-weight: 600; font-size: 23px;
    letter-spacing: 1.2px; line-height: 1.2;
  }
  .person-title { font-size: 16px; letter-spacing: 0.5px; margin-top: 1px; }

  .divider {
    position: absolute; left: 37px; right: 38px; top: 263px;
    height: 1px; background: var(--green);
  }

  .contacts {
    position: absolute; left: 37px; top: 281px;
    list-style: none; font-size: 16.5px; letter-spacing: 0.4px;
  }
  .contacts li { display: flex; align-items: center; gap: 8px; height: 26.5px; }
  .contacts svg { width: 12px; height: 12px; fill: var(--green); flex: none; }

  .address {
    position: absolute; right: 38px; top: 310px;
    text-align: right; font-size: 16.5px; letter-spacing: 0.4px; line-height: 22.5px;
    font-style: normal;
  }

  .brand-back {
    position: absolute; left: 0; right: 0; top: 150px;
    display: flex; flex-direction: column; align-items: center; gap: 16px;
    color: var(--green); font-weight: 700; font-size: 26px;
    letter-spacing: 0.6px; text-transform: uppercase;
  }
  .brand-back .brand-square { width: 34px; height: 34px; }
</style>
</head>
<body>
  <section class="card card-front">
    <div class="brand"><span class="brand-square"></span>Holloway Build Co.</div>

    <div class="name-accent"></div>
    <div class="person">
      <h1 class="person-name">CALVIN MARSH</h1>
      <p class="person-title">Managing Director</p>
    </div>

    <div class="divider"></div>

    <ul class="contacts">
      <li>
        <svg viewBox="0 0 24 24" aria-hidden="true"><path d="M6.6 10.8a15.1 15.1 0 0 0 6.6 6.6l2.2-2.2a1 1 0 0 1 1-.25 11.4 11.4 0 0 0 3.6.57 1 1 0 0 1 1 1V20a1 1 0 0 1-1 1A17 17 0 0 1 3 4a1 1 0 0 1 1-1h3.5a1 1 0 0 1 1 1c0 1.25.2 2.45.57 3.57a1 1 0 0 1-.25 1z"/></svg>
        0412 555 019
      </li>
      <li>
        <svg viewBox="0 0 24 24" aria-hidden="true"><path d="M2 9l10-6 10 6v11a1 1 0 0 1-1 1H3a1 1 0 0 1-1-1zm2 1.2V19h16v-8.8l-8 5z"/></svg>
        hello@hollowaybuild.com
      </li>
      <li>
        <svg viewBox="0 0 24 24" aria-hidden="true"><path d="M12 2a10 10 0 1 0 0 20 10 10 0 0 0 0-20zm-1 17.9A8 8 0 0 1 4.1 11l4.9 4.9v1a2 2 0 0 0 2 2zm6.9-2.5A2 2 0 0 0 16 16h-1v-3a1 1 0 0 0-1-1H8v-2h2a1 1 0 0 0 1-1V7h2a2 2 0 0 0 2-2v-.4a8 8 0 0 1 2.9 12.8z"/></svg>
        www.hollowaybuild.com
      </li>
    </ul>

    <address class="address">
      418 Ridgeway Avenue<br>
      Fairmont District 4470
    </address>
  </section>

  <section class="card card-back">
    <div class="brand-back"><span class="brand-square"></span>Holloway Build Co.</div>
  </section>
</body>
</html>
```